Web Design Project for Communications Agency

The design I need (PSD file) is for an agency offering specialised PR and communications services for customers in the healthcare sector.

OBJECTIVES OF THE WEBSITE:
1. To promote the agency's communication services
2. To position Solène Brivard as an industry leader, an expert in healthcare PR and communications by highlighting blogposts and social media.

WHAT I NEED:
1st, I need the design for the Home Page ONLY.
Once approved, I will need the other pages designed as well. (Here is prototype that we've already developed for the Website that will guide you in the design:
http://qorvelle.net/solenebrivard/)

VISUAL INSPIRATION
We want to give this Website a "Flat Design" look. Here are some websites for inspiration :
- http://tavrolinkworks.com/#!/process
- http://www.brindlemoss.co/
- http://quellaroft.com/

Also, reuse images found on the company's current Website :
http://www.solenebrivard.com/fr/index.html

HOMEPAGE MAIN ELEMENTS:
1. Main menu : 6 sections
Accueil | Agence | Services | Approche | Publications | Contact

2. Main Call To Action (big dark rectangle in prototype):
Can be slider or just an information bloc.

3. Publications récentes :
The 4 latest blog posts must be features on the homepage (will be linked with the "Publications" section)

4. Dynamic Footer :
Contains a Chirpline feed and a Subscribe to our Newsletter feature (revecez nos publications)

OTHER PAGES (to design once Homepage is approved)
- Agence (about us)
- Services (our team)
- Approche (our approach)
- Publications (blog articles)
- Contact (Contact us)

Industry/Entity Type

Communications

Requirements
Must have
• Please refer to prototype :
http://qorvelle.net/solenebrivard/
Must have ALL features present in prototype.

Also, must reuse this picture in the design : http://solenebrivard.com/static/images/home-big-box.jpg

Finally, you will find attached the company logo.

```html
<!DOCTYPE html>
<html lang="fr">
<head>
<meta charset="utf-8">
<title>Solène Brivard — Gestion d'enjeux, affaires publiques</title>
<link href="https://fonts.googleapis.com/css2?family=Fira+Sans:ital,wght@0,400;0,500;0,600;1,400&display=swap" rel="stylesheet">
<style>
:root{
  --red:#c0423b;
  --red-dark:#a8352f;
  --top:#f2f2f2;
  --ink:#333333;
  --muted:#666666;
  --hero:#262626;
  --foot:#3d3d3d;
  --foot-box:#2b2b2b;
  --panel:#f5f5f5;
  --line:#dddddd;
  --white:#ffffff;
}
*{box-sizing:border-box;margin:0;padding:0}
html,body{width:760px;height:1200px;overflow:hidden}
body{position:relative;background:var(--white);font-family:"Fira Sans",Arial,sans-serif;color:var(--ink)}
.abs{position:absolute}

/* header */
.site-header{left:0;top:0;width:760px;height:111px;background:var(--top)}
.brand{left:82px;top:14px;width:140px}
.brand-name{font-size:25px;line-height:27px;color:var(--red);font-weight:400}
.brand-tag{position:absolute;left:82px;top:83px;font-size:8.5px;line-height:10px;letter-spacing:.4px;font-weight:600;color:#555;text-transform:uppercase}
.lang{right:82px;top:11px;font-size:8.5px;font-weight:600;color:#444}
.lang .on{color:var(--red)}
.follow{left:561px;top:43px;font-size:8.5px;color:#555;font-weight:500}
.social{top:38px;width:21px;height:21px;border-radius:3px}
.social-fan{left:608px;background:#3b5a98}
.social-chirp{left:633px;background:#4ab3e3}
.social-link{left:658px;background:#2a6fae}
.nav-band{left:0;top:81px;width:760px;height:28px}
.main-nav{left:317px;top:81px;height:28px;display:flex;align-items:center;font-size:10px;font-weight:500;color:var(--white)}
.main-nav span{position:absolute;white-space:nowrap}

/* hero */
.hero{left:0;top:111px;width:760px;height:271px;background:var(--hero)}
.hero-visual{left:83px;top:143px;width:277px;height:197px;border:2px solid #e8e8e8;background:linear-gradient(160deg,#f7f7f7,#d9d9d9)}
.hero-title{left:377px;top:136px;width:320px;font-size:24.5px;line-height:32px;color:var(--white);font-weight:400}
.hero-btn{left:377px;top:288px;width:129px;height:32px;background:var(--red);border-radius:2px;color:var(--white);font-size:15px;line-height:32px;text-align:center}
.dot{top:358px;width:10px;height:10px;border-radius:50%;background:#777}
.dot.active{background:var(--white)}

/* publications */
.section-title{left:82px;top:399px;font-size:21px;color:var(--red);font-weight:400}
.pub-thumb{left:82px;width:192px;height:115px;border:3px solid var(--white);box-shadow:0 0 0 1px var(--line)}
.pub-card{left:294px;width:384px;height:121px;background:var(--panel);border:1px solid var(--line);border-radius:2px;padding:7px 14px 0 11px}
.pub-card::before{content:"";position:absolute;left:-7px;top:14px;border:7px solid transparent;border-left:0;border-right-color:var(--panel)}
.pub-title{font-size:12px;font-weight:500;color:#222;line-height:16px}
.pub-date{font-size:7.5px;font-style:italic;color:var(--red);line-height:11px;margin-top:1px}
.pub-text{font-size:7.3px;line-height:12.8px;color:var(--muted);margin-top:1px}
.read-more{display:inline-block;margin-top:7px;width:67px;height:19px;background:var(--red);color:var(--white);border-radius:2px;font-size:7.3px;font-weight:500;line-height:19px;text-align:center;text-transform:uppercase}

/* footer */
.footer{left:0;top:970px;width:760px;height:192px;background:var(--foot)}
.feed-title{left:82px;top:979px;font-size:19px;font-weight:600;color:var(--white)}
.feed-box{left:82px;top:1006px;width:292px;height:146px;background:var(--foot-box);border-radius:2px;padding:0 15px}
.tweet{font-size:7.5px;line-height:12.8px;color:#e6e6e6;padding:10px 0 11px;border-bottom:1px solid #444}
.tweet:last-child{border-bottom:0}
.tweet .tag{color:var(--red)}
.news-icon{left:388px;top:976px}
.news-title{left:422px;top:981px;font-size:14px;color:var(--white)}
.news-box{left:386px;top:1006px;width:292px;height:146px;background:var(--foot-box);border-radius:2px}
.field-label{left:399px;font-size:10px;color:#eee}
.field{left:399px;width:263px;height:20px;border-radius:3px;background:linear-gradient(#ffffff,#e6e6e6)}
.subscribe{left:574px;top:1119px;width:88px;height:20px;background:var(--red);border-radius:2px;color:var(--white);font-size:10px;line-height:20px;text-align:center}
.bottom-bar{left:0;top:1162px;width:760px;height:38px;background:var(--top)}
.copyright{left:82px;top:1176px;font-size:7.3px;color:#777}
.copyright .name{color:var(--red)}
</style>
</head>
<body>

<header class="site-header abs"></header>
<div class="brand abs"><div class="brand-name">solène<br>brivard</div></div>
<div class="brand-tag">Gestion d'enjeux<br>Affaires publiques</div>
<div class="lang abs"><span class="on">EN</span> &nbsp;|&nbsp; FR</div>
<div class="follow abs">Follow Us</div>
<div class="social social-fan abs" role="img" aria-label="Fanlink"></div>
<div class="social social-chirp abs" role="img" aria-label="Chirpline"></div>
<div class="social social-link abs" role="img" aria-label="Linkora"></div>

<svg class="nav-band abs" width="760" height="28" viewBox="0 0 760 28">
  <rect x="0" y="0" width="760" height="28" fill="#ffffff"/>
  <polygon points="172,0 760,0 760,28 191,28" fill="#c0423b"/>
  <line x1="82" y1="25" x2="103" y2="25" stroke="#c0423b" stroke-width="1"/>
</svg>
<nav class="main-nav abs">
  <span style="left:0">Accueil</span>
  <span style="left:57px">Agence</span>
  <span style="left:114px">Services</span>
  <span style="left:176px">Approche</span>
  <span style="left:245px">Publications</span>
  <span style="left:325px">Contact</span>
</nav>

<section class="hero abs"></section>
<div class="hero-visual abs" role="img" aria-label="Cube blanc aux faces marquées d'une croix rouge"></div>
<h1 class="hero-title abs">Cabinet-conseil en communications et affaires publiques spécialisé dans le secteur de la santé.</h1>
<div class="hero-btn abs">En Savior Plus</div>
<div class="dot active abs" style="left:353px"></div>
<div class="dot abs" style="left:368px"></div>
<div class="dot abs" style="left:382px"></div>
<div class="dot abs" style="left:397px"></div>

<h2 class="section-title abs">Publication récentes</h2>

<div class="pub-thumb abs" style="top:434px;background:linear-gradient(160deg,#e9e2da,#8a6a55)" role="img" aria-label="Mains levées dans une assemblée"></div>
<article class="pub-card abs" style="top:434px">
  <div class="pub-title">Titre de la publication</div>
  <div class="pub-date">23JULY 2013</div>
  <p class="pub-text">Lorem ipsum dolor sit amet, consectetur adipisicing elit, sed do eiusmod tempor incididunt ut labore et dolore magna aliqua. Ut enim ad minim veniam, quis nostrud exercitation ullamco laboris nisi ut aliquip ex ea commodo consequat. Duis aute irure dolor in reprehenderit in voluptate velit esse cillum dolore eu fugiat nulla pariatur.</p>
  <span class="read-more">Read more</span>
</article>

<div class="pub-thumb abs" style="top:568px;background:linear-gradient(180deg,#f2f2f2,#bdbdbd)" role="img" aria-label="Microphones de conférence de presse"></div>
<article class="pub-card abs" style="top:568px">
  <div class="pub-title">Titre de la publication</div>
  <div class="pub-date">23JULY 2013</div>
  <p class="pub-text">Lorem ipsum dolor sit amet, consectetur adipisicing elit, sed do eiusmod tempor incididunt ut labore et dolore magna aliqua. Ut enim ad minim veniam, quis nostrud exercitation ullamco laboris nisi ut aliquip ex ea commodo consequat. Duis aute irure dolor in reprehenderit in voluptate velit esse cillum dolore eu fugiat nulla pariatur.</p>
  <span class="read-more">Read more</span>
</article>

<div class="pub-thumb abs" style="top:702px;background:linear-gradient(150deg,#f4f4f4,#d8d8d8)" role="img" aria-label="Schéma manuscrit sur tableau blanc"></div>
<article class="pub-card abs" style="top:702px">
  <div class="pub-title">Titre de la publication</div>
  <div class="pub-date">23JULY 2013</div>
  <p class="pub-text">Lorem ipsum dolor sit amet, consectetur adipisicing elit, sed do eiusmod tempor incididunt ut labore et dolore magna aliqua. Ut enim ad minim veniam, quis nostrud exercitation ullamco laboris nisi ut aliquip ex ea commodo consequat. Duis aute irure dolor in reprehenderit in voluptate velit esse cillum dolore eu fugiat nulla pariatur.</p>
  <span class="read-more">Read more</span>
</article>

<div class="pub-thumb abs" style="top:837px;background:linear-gradient(160deg,#1a1a1a,#6a1a1a)" role="img" aria-label="Pièces de monnaie en gros plan"></div>
<article class="pub-card abs" style="top:837px">
  <div class="pub-title">Titre de la publication</div>
  <div class="pub-date">23JULY 2013</div>
  <p class="pub-text">Lorem ipsum dolor sit amet, consectetur adipisicing elit, sed do eiusmod tempor incididunt ut labore et dolore magna aliqua. Ut enim ad minim veniam, quis nostrud exercitation ullamco laboris nisi ut aliquip ex ea commodo consequat. Duis aute irure dolor in reprehenderit in voluptate velit esse cillum dolore eu fugiat nulla pariatur.</p>
  <span class="read-more">Read more</span>
</article>

<footer class="footer abs"></footer>
<div class="feed-title abs">chirpline</div>
<div class="feed-box abs">
  <p class="tweet">Velit esse cillum dolore eu fugiat nulla pariatur. Excepteur sint occaecat cupidatat non proident. <span class="tag">@SoleneBrivard #EnjeuSanté</span></p>
  <p class="tweet">Velit esse cillum dolore eu fugiat nulla pariatur. Excepteur sint occaecat cupidatat non proident. <span class="tag">@SoleneBrivard #EnjeuSanté</span></p>
  <p class="tweet">Velit esse cillum dolore eu fugiat nulla pariatur. Excepteur sint occaecat cupidatat non proident. <span class="tag">@SoleneBrivard #EnjeuSanté</span></p>
</div>

<svg class="news-icon abs" width="26" height="24" viewBox="0 0 26 24">
  <rect x="5" y="2" width="15" height="12" fill="#ffffff" transform="rotate(-12 12 8)"/>
  <polygon points="1,10 25,10 25,23 1,23" fill="#e8b53a"/>
  <polyline points="1,10 13,18 25,10" fill="none" stroke="#c99522" stroke-width="1"/>
</svg>
<div class="news-title abs">Recevez nos Publications</div>
<div class="news-box abs"></div>
<div class="field-label abs" style="top:1018px">Votre nom</div>
<div class="field abs" style="top:1036px"></div>
<div class="field-label abs" style="top:1066px">Votre courriel</div>
<div class="field abs" style="top:1084px"></div>
<div class="subscribe abs">Abonnez- vous</div>

<div class="bottom-bar abs"></div>
<div class="copyright abs">(c)2013 <span class="name">Solène Brivard</span>. Tous droits réservés.</div>

</body>
</html>
```